Need Help having my business card stand out

I am the owner of Birchway Canine Training and would like for my business cards to stand out. I have been trying to keep designing them myself but I can't get what I have in my head on the card. I will try my best to post templates that I like for inspirations. I want something unique but elegant. I don't want in to look cartoony or cheesy. It needs to pop in a pet shop but also in a coffee shop or gym.

Target Market(s)

Dog owners, Married ,No young kids Jr High school kids and up (maybe kids on the way) Executives, Stay at home moms/wives, Small business owners

Industry/Entity Type

Dog Training

Contact Information for Business Card

Lowell Spratt, 281-904-3376, info@birchwaycanine.example, www.birchwaycanine.example

Colors

Designer to choose colors to be used in the design.

Requirements
Must have
• my logo
Should not have
• Cursive lettering

```html
<!DOCTYPE html>
<html lang="en">
<head>
<meta charset="utf-8">
<title>Birchway Canine Training – Business Card</title>
<link href="https://fonts.googleapis.com/css2?family=Roboto:wght@400;500&display=swap" rel="stylesheet">
<style>
  :root {
    --backdrop: #2e2723;
    --card: #111111;
    --ink: #f4f4f4;
    --ink-soft: #d9d9d9;
    --icon-glyph: #111111;
  }
  * { margin: 0; padding: 0; box-sizing: border-box; }
  html, body { width: 1200px; height: 764px; overflow: hidden; }
  body {
    background: var(--backdrop);
    font-family: "Roboto", Arial, sans-serif;
    color: var(--ink);
    position: relative;
  }
  .card {
    position: absolute;
    top: 228px;
    width: 540px;
    height: 309px;
    background: var(--card);
    border-radius: 3px;
    box-shadow: 0 10px 30px rgba(0,0,0,.45);
  }
  .card--front { left: 40px; }
  .card--back { left: 620px; }

  .brand {
    position: absolute;
    display: flex;
    align-items: center;
    gap: 10px;
    font-weight: 500;
    color: var(--ink);
    letter-spacing: .5px;
  }
  .brand__dot {
    width: 14px; height: 14px;
    border: 2px solid var(--ink);
    border-radius: 50%;
    flex: none;
  }
  .brand__name { font-size: 17px; line-height: 1.15; text-align: left; }
  .card--front .brand { left: 150px; top: 58px; }
  .card--back .brand { right: 40px; top: 38px; }
  .card--back .brand__name { font-size: 14px; }

  .holder {
    position: absolute;
    left: 56px;
    top: 214px;
    font-size: 19px;
    font-weight: 400;
    letter-spacing: .5px;
    text-transform: uppercase;
  }
  .divider {
    position: absolute;
    left: 238px;
    top: 146px;
    width: 2px;
    height: 132px;
    background: var(--ink);
  }
  .contacts {
    position: absolute;
    left: 260px;
    top: 150px;
    list-style: none;
    font-size: 14.5px;
    color: var(--ink-soft);
  }
  .contacts li { display: flex; align-items: center; gap: 10px; height: 22px; }
  .contacts li.contacts__phone { margin-bottom: 22px; }
  .contacts svg { width: 14px; height: 14px; flex: none; }

  .site {
    position: absolute;
    left: 34px;
    bottom: 46px;
    font-size: 13px;
    color: var(--ink-soft);
  }
  .site-rule {
    position: absolute;
    left: 232px;
    right: 40px;
    bottom: 53px;
    height: 1px;
    background: var(--ink-soft);
  }
</style>
</head>
<body>
  <section class="card card--front" aria-label="Business card front">
    <div class="brand">
      <span class="brand__dot"></span>
      <span class="brand__name">Birchway Canine<br>Training</span>
    </div>
    <p class="holder">Lowell Spratt</p>
    <span class="divider"></span>
    <ul class="contacts">
      <li class="contacts__phone">
        <svg viewBox="0 0 14 14"><rect width="14" height="14" rx="2" fill="#f4f4f4"/><path d="M4 3.2l1.6-.2.8 2-1 .8a6 6 0 0 0 2.8 2.8l.8-1 2 .8-.2 1.6c-.1.5-.6.8-1.1.7A8 8 0 0 1 3.3 4.3c-.1-.5.2-1 .7-1.1z" fill="#111"/></svg>
        281-904-3376
      </li>
      <li>
        <svg viewBox="0 0 14 14"><rect width="14" height="14" rx="2" fill="#f4f4f4"/><rect x="3" y="4.5" width="8" height="5.5" fill="none" stroke="#111" stroke-width="1.1"/><path d="M3 4.7l4 3 4-3" fill="none" stroke="#111" stroke-width="1.1"/></svg>
        info@birchwaycanine.example
      </li>
      <li>
        <svg viewBox="0 0 14 14"><rect width="14" height="14" rx="2" fill="#f4f4f4"/><circle cx="7" cy="7" r="3.8" fill="none" stroke="#111" stroke-width="1.1"/><path d="M3.2 7h7.6M7 3.2c-1.6 2.2-1.6 5.4 0 7.6M7 3.2c1.6 2.2 1.6 5.4 0 7.6" fill="none" stroke="#111" stroke-width=".9"/></svg>
        www.birchwaycanine.example
      </li>
    </ul>
  </section>

  <section class="card card--back" aria-label="Business card back">
    <div class="brand">
      <span class="brand__dot"></span>
      <span class="brand__name">Birchway Canine<br>Training</span>
    </div>
    <p class="site">www.birchwaycanine.example</p>
    <span class="site-rule"></span>
  </section>
</body>
</html>
```